Need a landing page design updated

Need an existing landing page perfected, want it too look similar to one of Quorbel's landing pages in that it flows and is really aesthetically pleasing. The link to the landing page is below. I need this design updated asap. Please take the content directly from the page.

http://verdantmoxfl.com/residential-services/

Target Market(s)

High end residential landscape customers on the gulf coast of Florida (Clearwater area)

Industry/Entity Type

Landscape Gardening

Font styles to use
Sans Serif
Decorative

Requirements
Must have
• I want to keep the written content the same on on the landing page, but would like to work on making both aesthetically appealing to the consumer. This is for high end residential clients on the gulf coast of florida, so think palm trees and sunny beaches with beautiful houses and gorgeous landscapes....look through www.verdantmoxfl.com home page for an example of the houses we landscape.
Nice to have
• Would like it to flow as you scroll similar to Quorbel's landing pages.
• Look at how Quorbel's landing page flows, want similar here.....
• https://www.quorbel.com/zentaphone-v/
Should not have
• this landing page must be beautiful and must make a lot of sense as you scroll, am looking for a work of art....please do not submit generic templates or anything that can be easily done....I need real artistry.

```html
<!DOCTYPE html>
<html lang="en">
<head>
<meta charset="utf-8">
<title>Verdantmox — Residential Landscaping</title>
<link href="https://fonts.googleapis.com/css2?family=Open+Sans:wght@400;600;700&display=swap" rel="stylesheet">
<style>
:root{
  --blue:#1a9bd7;
  --blue-deep:#1f8fc8;
  --teal-deep:#0f4f6d;
  --band-blue:#1c86b6;
  --footer-blue:#29a3d4;
  --ink:#222;
  --white:#fff;
  --light:#ececec;
  --dark:#1d1f24;
}
*{box-sizing:border-box;margin:0;padding:0}
html,body{width:1200px;height:4444px;overflow:hidden}
body{font-family:"Open Sans",Arial,sans-serif;color:var(--ink);position:relative;background:var(--white)}
.section{position:absolute;left:0;width:1200px;overflow:hidden}
.backdrop{position:absolute;inset:0}
.center{position:absolute;left:0;width:1200px;text-align:center}

/* header */
.site-header{top:0;height:95px;background:var(--white)}
.brand{position:absolute;left:92px;top:30px;display:flex;align-items:center;gap:10px;font-size:26px;font-weight:600;color:#1a6f9e;letter-spacing:1px}
.brand-dot{width:14px;height:14px;border-radius:50%;background:var(--blue)}
.contact{position:absolute;right:92px;top:38px;text-align:right;font-size:12px;line-height:17px;color:#333}
.contact .label{color:var(--blue)}
.main-nav{top:95px;height:35px;background:var(--blue);display:flex;align-items:center;padding-left:92px;gap:26px}
.main-nav a{color:var(--white);font-size:11px;font-weight:700;text-decoration:none;letter-spacing:.3px}

/* hero */
.hero{top:130px;height:474px}
.hero .backdrop{background:linear-gradient(180deg,#6f8aa0 0%,#8b9aa2 35%,#7b8a6a 65%,#5f6656 100%)}
.hero h1{top:150px;font-size:50px;font-weight:400;color:var(--white)}
.hero p{top:212px;font-size:22px;font-weight:600;line-height:36px;color:var(--white)}

/* leisure */
.leisure{top:604px;height:383px}
.leisure .backdrop{background:radial-gradient(ellipse at 60% 40%,#3a3d33 0%,#23251f 60%,#1a1b18 100%)}
.leisure .lead{top:103px;font-size:18px;color:var(--white)}
.leisure .body{top:145px;font-size:21px;line-height:38px;color:var(--white)}
.leisure .punch{top:234px;font-size:29px;font-weight:700;color:var(--white)}

/* intro */
.intro{top:987px;height:169px;background:var(--light)}
.intro .small{top:41px;font-size:17px;color:#333}
.intro .big{top:70px;font-size:21px;line-height:31px;color:#222}

/* compare */
.compare{top:1156px;height:435px}
.col{position:absolute;top:0;height:435px;padding:52px 0 0 86px;color:var(--white)}
.col.generic{left:0;width:601px;background:var(--blue-deep)}
.col.tailored{left:601px;width:599px;background:var(--teal-deep);padding-left:midpoint}
.col.tailored{padding-left:44px}
.col h2{font-size:28px;font-weight:400;margin-bottom:26px}
.col ul{list-style:none;width:430px}
.col li{position:relative;padding-left:30px;font-size:16px;line-height:25px;margin-bottom:14px}
.col li svg{position:absolute;left:0;top:5px}

/* experts */
.experts{top:1591px;height:433px}
.experts .backdrop{background:linear-gradient(180deg,#2c2f2a 0%,#3b4036 45%,#2a2c29 100%)}
.experts h2{top:112px;font-size:22px;font-weight:700;line-height:37px;color:var(--white)}
.experts p{font-size:16px;color:var(--white)}
.experts .p1{top:209px;line-height:27px}
.experts .p2{top:285px}

/* privacy */
.privacy{top:2024px;height:504px}
.privacy .backdrop{background:linear-gradient(135deg,#f4f4f4 0%,#e6e6e6 50%,#f2f2f2 100%)}
.privacy-card{position:absolute;left:148px;top:103px;width:895px;height:297px;background:var(--white);box-shadow:0 4px 18px rgba(0,0,0,.25);display:flex}
.privacy-text{width:495px;padding:48px 40px 0 40px}
.privacy-text .q{font-size:24px;line-height:35px;color:#222;margin-bottom:22px}
.privacy-text .a{font-size:19px;font-weight:700;line-height:29px;color:#222;text-align:justify}
.privacy-photo{width:400px;height:297px;background:linear-gradient(160deg,#7a9a3c 0%,#4e6f25 55%,#3b5520 100%)}

/* benefits */
.benefits{top:2528px;height:539px;background:var(--dark)}
.benefits h2{top:117px;font-size:28px;font-weight:400;color:var(--white)}
.benefit{position:absolute;top:219px;width:290px;text-align:center;color:var(--white)}
.benefit .icon{width:106px;height:106px;margin:0 auto 22px;border-radius:50%;background:var(--blue);border:3px solid #5fc0ea;display:flex;align-items:center;justify-content:center}
.benefit p{font-size:15px;line-height:22px}

/* testimonials */
.testimonials{top:3067px;height:450px}
.testimonials .backdrop{background:linear-gradient(180deg,#2d3a2a 0%,#263222 50%,#1e241b 100%)}
.testimonials h2{top:103px;font-size:25px;font-weight:700;color:var(--white)}
.testimonials .sub{top:148px;font-size:20px;color:var(--white)}
.quote{position:absolute;top:258px;font-size:16px;line-height:27px;color:var(--white);text-align:justify}
.quote .mark{font-size:26px;color:#9fd3ee;font-family:Georgia,serif;line-height:0}
.quote.one{left:133px;width:415px}
.quote.two{left:646px;width:427px}

/* flaws */
.flaws{top:3517px;height:335px;background:var(--band-blue)}
.flaws .head{top:85px;font-size:29px;line-height:38px;color:var(--white)}
.flaws ol{position:absolute;top:175px;left:0;width:1200px;text-align:center;list-style:none;font-size:18px;line-height:35px;color:var(--white)}

/* cta */
.cta{top:3852px;height:495px}
.cta .backdrop{background:linear-gradient(180deg,#232a22 0%,#1f241d 60%,#191c18 100%)}
.cta .head{top:115px;font-size:28px;line-height:42px;color:var(--white)}
.cta .strong{top:215px;font-size:28px;font-weight:700;color:var(--white)}
.lead-form{position:absolute;top:302px;left:163px;display:flex;gap:18px}
.field{width:317px;height:70px;border:1px solid rgba(255,255,255,.5);background:rgba(255,255,255,.04);color:var(--white);font-size:16px;padding:0 20px;display:flex;align-items:center;font-family:inherit}
.field.contact-field{width:314px}
.submit{width:213px;height:70px;background:var(--blue);color:var(--white);font-size:19px;display:flex;align-items:center;justify-content:center;border:none;font-family:inherit}

/* footer */
.site-footer{top:4347px;height:97px;background:var(--footer-blue)}
.site-footer p{top:38px;font-size:16px;color:var(--white)}
</style>
</head>
<body>

<header class="section site-header">
  <div class="brand"><span class="brand-dot"></span>VERDANTMOX</div>
  <div class="contact">
    <div><span class="label">Call Us Now On:</span> 727-555-0148</div>
    <div>Client Portal | Get A Free Quote</div>
  </div>
</header>
<nav class="section main-nav">
  <a>HOME</a><a>ABOUT US</a><a>RESIDENTIAL</a><a>COMMERCIAL</a><a>BLOG</a><a>CONTACT US</a>
</nav>

<section class="section hero">
  <div class="backdrop" role="img" aria-label="Sunny palm-lined street with a white house and manicured lawn"></div>
  <h1 class="center">Let’s guess:</h1>
  <p class="center">You don’t have an abundance of free time. And, you simply don’t want to<br>spend the little time you have – mowing a lawn and pruning the plants.</p>
</section>

<section class="section leisure">
  <div class="backdrop" role="img" aria-label="Dimmed garden scene at dusk"></div>
  <p class="center lead">You would probably like to spend that time the way you should, instead.</p>
  <p class="center body">Enjoying the sunset in the privacy of your garden, watching a favorite TV show while lying<br>on a hammock, or throwing an occasional BBQ party with your friends and loved ones.</p>
  <p class="center punch">Right?</p>
</section>

<section class="section intro">
  <p class="center small">Getting an outdoor area of your dreams is not that difficult, nor expensive.</p>
  <p class="center big">You can make this happen by getting a help from a landscaping company<br>that offers tailor-made services.</p>
</section>

<section class="section compare">
  <div class="col generic">
    <h2>Generic landscaping services:</h2>
    <ul>
      <li><svg width="17" height="17" viewBox="0 0 17 17"><circle cx="8.5" cy="8.5" r="8.5" fill="#fff"/><path d="M4.5 8.8l2.6 2.6 5.4-5.4" stroke="#1f8fc8" stroke-width="2" fill="none"/></svg>You pay for the bundle of services, regardless of whether you actually need them</li>
      <li><svg width="17" height="17" viewBox="0 0 17 17"><circle cx="8.5" cy="8.5" r="8.5" fill="#fff"/><path d="M4.5 8.8l2.6 2.6 5.4-5.4" stroke="#1f8fc8" stroke-width="2" fill="none"/></svg>You get a generic service, not adjusted to the specific needs of your outdoor area</li>
      <li><svg width="17" height="17" viewBox="0 0 17 17"><circle cx="8.5" cy="8.5" r="8.5" fill="#fff"/><path d="M4.5 8.8l2.6 2.6 5.4-5.4" stroke="#1f8fc8" stroke-width="2" fill="none"/></svg>The field team thinks of your property as just another task they have to complete</li>
    </ul>
  </div>
  <div class="col tailored">
    <h2>Tailor-made landscaping services:</h2>
    <ul>
      <li><svg width="17" height="17" viewBox="0 0 17 17"><circle cx="8.5" cy="8.5" r="8.5" fill="#fff"/><path d="M4.5 8.8l2.6 2.6 5.4-5.4" stroke="#0f4f6d" stroke-width="2" fill="none"/></svg>You pay only for the services your yard really needs.</li>
      <li><svg width="17" height="17" viewBox="0 0 17 17"><circle cx="8.5" cy="8.5" r="8.5" fill="#fff"/><path d="M4.5 8.8l2.6 2.6 5.4-5.4" stroke="#0f4f6d" stroke-width="2" fill="none"/></svg>You get your garden’s specific issues solved, and specific requirements met</li>
      <li><svg width="17" height="17" viewBox="0 0 17 17"><circle cx="8.5" cy="8.5" r="8.5" fill="#fff"/><path d="M4.5 8.8l2.6 2.6 5.4-5.4" stroke="#0f4f6d" stroke-width="2" fill="none"/></svg>The field team members take their time working on your property</li>
      <li><svg width="17" height="17" viewBox="0 0 17 17"><circle cx="8.5" cy="8.5" r="8.5" fill="#fff"/><path d="M4.5 8.8l2.6 2.6 5.4-5.4" stroke="#0f4f6d" stroke-width="2" fill="none"/></svg>They get to learn all about your vision – and make it a reality</li>
    </ul>
  </div>
</section>

<section class="section experts">
  <div class="backdrop" role="img" aria-label="Dark, softly lit garden with trees and lawn"></div>
  <h2 class="center">Why should you care that Verdantmox employs&nbsp; the leading industry experts and<br>uses modern, eco-friendly technical solutions?</h2>
  <p class="center p1">That is why we’re able to transform your lawn into a green carpet and get your plants in a perfect<br>health. All while keeping your vision and your budget on our minds.</p>
  <p class="center p2">That is why our services actually enable you to reduce the operating expenses.</p>
</section>

<section class="section privacy">
  <div class="backdrop"></div>
  <div class="privacy-card">
    <div class="privacy-text">
      <p class="q">Do you worry our services are going to disturb you while trying to unwind in the privacy of your own garden?</p>
      <p class="a">Our Client Service Operators Build A Schedule Around Your Needs –Designed Not To Disturb You At All.</p>
    </div>
    <div class="privacy-photo" role="img" aria-label="Person relaxing on a grassy lawn with small white flowers"></div>
  </div>
</section>

<section class="section benefits">
  <h2 class="center">More benefits of having a well-maintained yard:</h2>
  <div class="benefit" style="left:119px">
    <div class="icon"><svg width="50" height="44" viewBox="0 0 50 44"><rect x="4" y="28" width="8" height="14" fill="#fff"/><rect x="16" y="22" width="8" height="20" fill="#fff"/><rect x="28" y="16" width="8" height="26" fill="#fff"/><rect x="40" y="8" width="8" height="34" fill="#fff"/><path d="M4 20L18 10l10 6L44 2" stroke="#fff" stroke-width="3" fill="none"/></svg></div>
    <p>In some cases, a great-looking lawn can increase your property’s value up to 20%.</p>
  </div>
  <div class="benefit" style="left:456px">
    <div class="icon"><svg width="50" height="46" viewBox="0 0 50 46"><path d="M25 3L4 21h6v22h30V21h6z" fill="none" stroke="#fff" stroke-width="3"/><circle cx="25" cy="29" r="8" fill="#fff"/></svg></div>
    <p>Your lawn and plants reduce the energy consumption – countering the warming effects of paved surfaces.</p>
  </div>
  <div class="benefit" style="left:791px">
    <div class="icon"><svg width="50" height="40" viewBox="0 0 50 40"><rect x="4" y="14" width="24" height="12" fill="#fff"/><path d="M28 4l18 16-18 16z" fill="#fff"/></svg></div>
    <p>They act as giant dust filters, increasing air quality, and removing carbon dioxide from the atmosphere</p>
  </div>
</section>

<section class="section testimonials">
  <div class="backdrop" role="img" aria-label="Dim photo of a house and lawn framed by trees"></div>
  <h2 class="center">At Verdantmox, we do more than just keeping your garden in pristine shape.</h2>
  <p class="center sub">This is what some of our long-term clients say about our approach:</p>
  <p class="quote one"><span class="mark">“</span> We are delighted with your landscaping, both with the design and implementation. It’s not very often these days that work exceeds expectations. <span class="mark">”</span></p>
  <p class="quote two"><span class="mark">“</span> Verdantmox are efficient, on-time, responsive, provide fair pricing, do outstanding work, have great people, and actually follow up on their work. <span class="mark">”</span></p>
</section>

<section class="section flaws">
  <p class="center head">Do our services have flaws?<br>Yes. They have two giant ones.</p>
  <ol>
    <li>1. Your “new” garden will get all of your neighbors jealous.</li>
    <li>2. Your friends will probably start inviting&nbsp; themselves over more frequently.</li>
  </ol>
</section>

<section class="section cta">
  <div class="backdrop" role="img" aria-label="Dark garden scene with lawn and shrubs"></div>
  <p class="center head">So, what’s the next step to enriching your living area?<br>And getting you a garden from your dreams.</p>
  <p class="center strong">It’s simple, just book a no-obligations consultation</p>
  <form class="lead-form">
    <div class="field">Name</div>
    <div class="field contact-field">E-mail or Phone</div>
    <div class="submit">Get Started</div>
  </form>
</section>

<footer class="section site-footer">
  <p class="center">Copyright 2017 Verdantmox All Rights Reserved</p>
</footer>

</body>
</html>
```